Business cards and stationary design

We just completed the design of our new logo and we need to print new business cards and letterhead for our nonprofit. We are looking for a fresh new design that shows off our new logo. On letterhead, we must have a column on the right or left to include our Board of Directors (up to 45 names) (see attachment)

Industry/Entity Type

Non-Profit

Contact Information for Business Card

Standard business card with name, title, Company name, mailing address phone numbers, email address and website. Tagline on back "Bringing the homeless home"

Font styles to use
Sans Serif

Requirements
Must have
• include pertinent information above
• new logo
• fonts compatible with logo
• should use logo colors only
Nice to have
• tag lines

```html
<!DOCTYPE html>
<html lang="en">
<head>
<meta charset="utf-8">
<title>Homeward Center – Business Card</title>
<link rel="stylesheet" href="https://fonts.googleapis.com/css2?family=Courier+Prime:wght@400;700&family=Lato:wght@400&display=swap">
<style>
  :root {
    --stage: #000000;
    --paper: #ffffff;
    --teal: #1a7b94;
    --red: #e8212e;
    --back-red: #ec1c24;
    --ink: #222222;
  }
  html, body {
    margin: 0;
    padding: 0;
    width: 1200px;
    height: 900px;
    overflow: hidden;
    background: var(--stage);
  }
  .canvas {
    position: relative;
    width: 1200px;
    height: 900px;
  }
  .card {
    position: absolute;
    top: 275px;
    width: 477px;
    height: 294px;
    box-sizing: border-box;
    overflow: hidden;
  }
  .card-front {
    left: 116px;
    background: var(--paper);
    border-radius: 0 46px 0 46px;
  }
  .card-back {
    left: 622px;
    border-radius: 46px 0 46px 0;
  }
  .brand {
    position: absolute;
    right: 26px;
    top: 74px;
    display: flex;
    align-items: center;
    gap: 10px;
    font-family: "Courier Prime", "Courier New", monospace;
    font-weight: 400;
    font-size: 28px;
    letter-spacing: -0.5px;
    color: var(--teal);
    white-space: nowrap;
  }
  .brand-dot {
    width: 16px;
    height: 16px;
    border-radius: 50%;
    background: var(--teal);
  }
  .person-name {
    position: absolute;
    left: 24px;
    top: 168px;
    margin: 0;
    font-family: "Courier Prime", "Courier New", monospace;
    font-weight: 700;
    font-size: 18px;
    color: var(--teal);
  }
  .person-role {
    position: absolute;
    left: 26px;
    right: 26px;
    top: 187px;
    display: flex;
    align-items: center;
    gap: 2px;
    font-family: "Lato", Arial, sans-serif;
    font-size: 14px;
    color: var(--red);
  }
  .person-role::after {
    content: "";
    flex: 1;
    height: 1px;
    background: var(--red);
    margin-top: 3px;
  }
  .contact-list {
    position: absolute;
    left: 28px;
    top: 220px;
    margin: 0;
    padding: 0;
    list-style: none;
    font-family: "Lato", Arial, sans-serif;
    font-size: 14px;
    line-height: 17.5px;
    color: var(--ink);
  }
  .contact-list li {
    display: flex;
    align-items: center;
    gap: 3px;
  }
  .contact-icon {
    width: 11px;
    height: 11px;
    fill: var(--teal);
  }
  .mailing-address {
    position: absolute;
    right: 27px;
    top: 237px;
    margin: 0;
    text-align: right;
    font-family: "Lato", Arial, sans-serif;
    font-style: normal;
    font-size: 14px;
    line-height: 17.5px;
    color: var(--ink);
  }
  .back-pattern {
    position: absolute;
    inset: 0;
    background: var(--back-red);
  }
  .back-brand {
    position: absolute;
    left: 0;
    right: 0;
    top: 120px;
    text-align: center;
    font-family: "Courier Prime", "Courier New", monospace;
    font-weight: 400;
    font-size: 34px;
    letter-spacing: -0.5px;
    color: var(--paper);
  }
</style>
</head>
<body>
<main class="canvas">
  <section class="card card-front">
    <div class="brand"><span class="brand-dot"></span>homeward center</div>

    <h1 class="person-name">Daniel Hayes</h1>
    <div class="person-role">Managing Director</div>

    <ul class="contact-list">
      <li>
        <svg class="contact-icon" viewBox="0 0 12 12"><path d="M1 4c0-2 2-3 5-3s5 1 5 3v1H8.5V3.8H3.5V5H1zM3 6h6l2 3v2H1V9z"/></svg>
        444 555 7210
      </li>
      <li>
        <svg class="contact-icon" viewBox="0 0 12 12"><path d="M1 2.5h10v7H1z"/><path d="M1 2.5l5 4 5-4" fill="none" stroke="#fff" stroke-width="1"/></svg>
        info@youremail.com
      </li>
      <li>
        <svg class="contact-icon" viewBox="0 0 12 12"><circle cx="6" cy="6" r="5.5"/><path d="M3 4h3v3H4zM7 7h2v2H7z" fill="#fff"/></svg>
        www.websitename.com
      </li>
    </ul>

    <address class="mailing-address">421, Address line here<br>Country Name,45452</address>
  </section>

  <section class="card card-back">
    <div class="back-pattern" role="img" aria-label="Repeating pattern of small house motifs in a lighter red"></div>
    <div class="back-brand">homeward center</div>
  </section>
</main>
</body>
</html>
```